Working Capital graphics

Our business advisory firm requires 9 images to be re-created and improved in the branding of our business.

The 9 images have been uploaded below and the colours and branding of the business can be found at the website www.tallowmereadvisory.com.au

```html
<!DOCTYPE html>
<html lang="en">
<head>
<meta charset="UTF-8">
<title>Payables Drivers</title>
<link href="https://fonts.googleapis.com/css2?family=Montserrat:ital,wght@0,700;1,700;1,800&display=swap" rel="stylesheet">
<style>
  :root {
    --canvas: #ffffff;
    --ink: #0b0b0b;
    --brand-blue: #55a7dc;
    --accent-orange: #f29b42;
    --number-ink: #ffffff;
    --connector: #111111;
  }
  html, body {
    margin: 0;
    padding: 0;
    overflow: hidden;
    background: var(--canvas);
  }
  .canvas {
    position: relative;
    width: 1200px;
    height: 1000px;
    overflow: hidden;
    background: var(--canvas);
    font-family: "Montserrat", Arial, sans-serif;
    color: var(--ink);
  }
  .page-title {
    position: absolute;
    left: 44px;
    top: 166px;
    margin: 0;
    font-size: 54px;
    font-weight: 800;
    font-style: italic;
    letter-spacing: 0.5px;
  }
  .column-heading {
    position: absolute;
    left: 644px;
    width: 200px;
    top: 164px;
    margin: 0;
    text-align: center;
    font-size: 35px;
    font-weight: 700;
  }
  .hub {
    position: absolute;
    left: 38px;
    top: 418px;
    width: 236px;
    height: 231px;
    background: var(--brand-blue);
    display: flex;
    align-items: center;
    justify-content: center;
    text-align: center;
    font-size: 28px;
    font-weight: 700;
    font-style: italic;
    line-height: 1.3;
  }
  .connectors {
    position: absolute;
    left: 0;
    top: 0;
  }
  .driver {
    position: absolute;
    left: 378px;
    width: 718px;
    height: 80px;
  }
  .driver-bar {
    position: absolute;
    left: 40px;
    right: 0;
    top: 8px;
    height: 64px;
    background: var(--brand-blue);
    display: flex;
    align-items: center;
    justify-content: center;
    font-size: 26px;
    font-weight: 700;
    font-style: italic;
    padding-left: 24px;
    box-sizing: border-box;
  }
  .driver-number {
    position: absolute;
    left: 0;
    top: 0;
    width: 80px;
    height: 80px;
    border-radius: 50%;
    background: var(--accent-orange);
    color: var(--number-ink);
    display: flex;
    align-items: center;
    justify-content: center;
    font-size: 44px;
    font-weight: 800;
    font-style: italic;
    letter-spacing: -2px;
    z-index: 1;
  }
</style>
</head>
<body>
<main class="canvas">
  <h1 class="page-title">Payables</h1>
  <h2 class="column-heading">Drivers</h2>

  <div class="hub">Payables<br>Drivers</div>

  <svg class="connectors" width="1200" height="1000" aria-hidden="true">
    <g stroke="var(--connector)" stroke-width="2" fill="none">
      <line x1="274" y1="535" x2="380" y2="535"/>
      <line x1="352" y1="291" x2="352" y2="776"/>
      <line x1="351" y1="291" x2="380" y2="291"/>
      <line x1="351" y1="411" x2="380" y2="411"/>
      <line x1="351" y1="655" x2="380" y2="655"/>
      <line x1="351" y1="776" x2="380" y2="776"/>
    </g>
  </svg>

  <div class="driver" style="top:251px">
    <span class="driver-number">14</span>
    <div class="driver-bar">Reduce early payments</div>
  </div>
  <div class="driver" style="top:376px">
    <span class="driver-number">15</span>
    <div class="driver-bar">Reduce over-rides</div>
  </div>
  <div class="driver" style="top:495px">
    <span class="driver-number">16</span>
    <div class="driver-bar">Reduce vendor credits</div>
  </div>
  <div class="driver" style="top:615px">
    <span class="driver-number">17</span>
    <div class="driver-bar">Increase PO vendor terms</div>
  </div>
  <div class="driver" style="top:736px">
    <span class="driver-number">18</span>
    <div class="driver-bar">Increase invoice only terms</div>
  </div>
</main>
</body>
</html>
```